New Business Card Design for Manufacturing

We are an engineering/manufacturing company that offers Advanced machining/assembly/engineering services, as well as innovative products for the heavy duty engine cooling markets.

We are looking to get a new business card designed that is clean and modern looking, but still fits the wide range of technical/skilled work we do.

- We hope to use this design as the base for other design work in new Presentations, web, and print work.

Industry/Entity Type

Engineering

Contact Information for Business Card

Our preferred color of blue is (RGB) 22/71/159 but can vary slightly from that color. Our content will be our Logo and full company name (Vantrell Forge Works, Inc.), company address, name, job title, phone number with extension, cell number, fax number, website, and email address on the cards.
We'd like the full company name next to the logo, but we are open to other interpretations of that layout.
Preferably, we would like the back side to be clean with just our logo, and the front to contain all of the contact information.

Colors
2f74b4
0355a3
85abd2

Requirements
Must have
• - Logo, company name, needed content - We are open to interpretation beyond that.
• - Standard size business card.
• - Horizontal orientation.
• - Enough space for lengthy names / job titles (for example, a job title could read "Directory of Human Resources" or "V.P. of Governmental Affairs"). We need this to look clean, whether the title be short (CEO) or long (as described above).

```html
<!DOCTYPE html>
<html lang="en">
<head>
<meta charset="utf-8">
<title>Vantrell Forge Works – Business Card</title>
<link rel="stylesheet" href="https://fonts.googleapis.com/css2?family=Fira+Sans:wght@400;500;800&family=Open+Sans:wght@400&display=swap">
<style>
  :root {
    --brand-blue: #0355a3;
    --deep-blue: #16479f;
    --ink: #3a3a3a;
    --muted-grey: #7c8288;
    --card-white: #fbfbfb;
    --card-black: #0b0b0b;
    --canvas: #e4e4e4;
  }
  * { margin: 0; padding: 0; box-sizing: border-box; }
  html, body { width: 1200px; height: 576px; overflow: hidden; }
  body { background: var(--canvas); position: relative; font-family: "Open Sans", sans-serif; }

  .card {
    position: absolute;
    top: 138px;
    width: 484px;
    height: 294px;
    border-radius: 14px;
    overflow: hidden;
  }
  .card--back { left: 82px; background: var(--card-black); }
  .card--front { left: 602px; background: var(--card-white); border: 1px solid #d4d4d4; }

  .back-wordmark {
    position: absolute;
    inset: 0;
    display: flex;
    align-items: center;
    justify-content: center;
    font-family: "Fira Sans", sans-serif;
    font-weight: 800;
    font-size: 58px;
    letter-spacing: 2px;
    color: #ffffff;
  }

  .front-wordmark {
    position: absolute;
    left: 24px;
    top: 34px;
    font-family: "Fira Sans", sans-serif;
    font-weight: 800;
    font-size: 42px;
    letter-spacing: 1.5px;
    color: var(--brand-blue);
    line-height: 1;
  }

  .person { position: absolute; left: 25px; top: 176px; }
  .person__name {
    font-family: "Fira Sans", sans-serif;
    font-weight: 500;
    font-size: 19px;
    color: var(--deep-blue);
    line-height: 1.2;
  }
  .person__title { font-size: 12px; color: var(--ink); margin-top: 2px; }
  .person__address { font-size: 12px; color: var(--ink); line-height: 1.5; margin-top: 16px; }

  .company { position: absolute; left: 264px; top: 160px; }
  .company__name {
    font-family: "Fira Sans", sans-serif;
    font-weight: 500;
    font-size: 13px;
    color: var(--deep-blue);
    margin-bottom: 9px;
  }
  .contact-list { list-style: none; }
  .contact-list li {
    display: flex;
    align-items: center;
    gap: 8px;
    font-size: 12px;
    color: var(--ink);
    line-height: 16.5px;
    margin-left: 6px;
  }
  .contact-list svg { width: 10px; height: 10px; fill: var(--deep-blue); flex: none; }

  .footer-band { position: absolute; left: 0; bottom: 0; width: 484px; height: 31px; }
  .footer-web {
    position: absolute;
    left: 264px;
    bottom: 8px;
    font-size: 12px;
    color: #ffffff;
  }
</style>
</head>
<body>

  <section class="card card--back" aria-label="Card back">
    <div class="back-wordmark">VANTRELL</div>
  </section>

  <section class="card card--front" aria-label="Card front">
    <div class="front-wordmark">VANTRELL</div>

    <div class="person">
      <p class="person__name">Marlow Keane</p>
      <p class="person__title">Managing Director</p>
      <p class="person__address">418 Foundry Row, Brackenfield,<br>OH 44512</p>
    </div>

    <div class="company">
      <p class="company__name">Vantrell Forge Works, Inc.</p>
      <ul class="contact-list">
        <li>
          <svg viewBox="0 0 10 10" aria-hidden="true"><path d="M1 3.5C1 2 2.5 1 5 1s4 1 4 2.5L7.5 4 7 3H3L2.5 4zM2.5 5h5L8.5 9h-7z"/></svg>
          330-555-0142 (VFW)
        </li>
        <li>
          <svg viewBox="0 0 10 10" aria-hidden="true"><path d="M3 0.5h4a1 1 0 0 1 1 1v7a1 1 0 0 1-1 1H3a1 1 0 0 1-1-1v-7a1 1 0 0 1 1-1zM3 2v5h4V2zM5 7.6a.6.6 0 1 0 0 1.2.6.6 0 0 0 0-1.2z"/></svg>
          330-555-0187
        </li>
        <li>
          <svg viewBox="0 0 10 10" aria-hidden="true"><path d="M3 0.5h4v2.5H3zM1 3.5h8v4H7.5v2h-5v-2H1zM3.3 6.5v2.3h3.4V6.5z"/></svg>
          330-555-0199
        </li>
        <li>
          <svg viewBox="0 0 10 10" aria-hidden="true"><path d="M0.5 2h9v6h-9zM1.3 2.6 5 5.6l3.7-3z" fill-rule="evenodd"/></svg>
          m.keane@vantrellforge.com
        </li>
      </ul>
    </div>

    <svg class="footer-band" viewBox="0 0 484 31" aria-hidden="true">
      <rect x="0" y="17" width="226" height="14" fill="var(--muted-grey)"/>
      <path d="M232 0H484V31H219Z" fill="var(--brand-blue)"/>
    </svg>
    <p class="footer-web">www.vantrellforge.com</p>
  </section>

</body>
</html>
```